I need a fresh looking, exciting and loaded design for Full service Restaurant

We need a web design for our restaurant, which offers full service Pakistani and Indian food in PA, USA. Design should be elegant, simplified so customers can navigate easily and order food online for catering as well as delivery. We need loads of pictures and room to grow. I already have a web address via vemrilo.com. It should include SSL and e-commerce for ordering food.
Be original and be creative and make it a fun site :)

```html
<!DOCTYPE html>
<html lang="en">
<head>
<meta charset="utf-8">
<title>Saffron Lane – Pakistani &amp; Indian Cuisine</title>
<link href="https://fonts.googleapis.com/css2?family=Roboto+Slab:wght@400;700&family=Lato:wght@400;700&family=Montserrat:wght@400;700&display=swap" rel="stylesheet">
<style>
:root{
  --red:#d0191b;
  --green:#1e4d0b;
  --green-dark:#153a06;
  --ink:#2a2a2a;
  --text:#6b6b6b;
  --muted:#9aa3ad;
  --page:#f3f3f3;
  --card:#f5f6f8;
  --white:#ffffff;
  --black:#050505;
}
*{margin:0;padding:0;box-sizing:border-box}
html,body{width:960px;height:1200px;overflow:hidden;background:var(--page);font-family:'Lato',sans-serif}
.site{position:relative;width:960px;height:1200px}
.sheet{position:absolute;left:70px;top:0;width:820px;height:1138px;background:var(--white);box-shadow:0 0 8px rgba(0,0,0,.06)}
.brand{position:absolute;left:80px;top:22px;display:flex;align-items:center;gap:8px}
.brand-dot{width:22px;height:22px;border-radius:50%;background:var(--green)}
.brand-name{font-family:'Roboto Slab',serif;font-weight:700;font-size:24px;color:var(--red)}
.nav{position:absolute;right:78px;top:34px;display:flex;gap:21px;font-family:'Roboto Slab',serif;font-size:12.5px;color:var(--ink)}
.nav .active{color:var(--red)}
.hero{position:absolute;left:80px;top:80px;width:800px;height:347px;border:2px solid #ddd;
  background:radial-gradient(ellipse at 30% 20%,#c8422a 0%,transparent 35%),radial-gradient(ellipse at 45% 55%,#c78a1c 0%,transparent 30%),radial-gradient(ellipse at 70% 80%,#6a2a14 0%,transparent 40%),linear-gradient(135deg,#4a3224,#2b1d14 60%,#5a2a16)}
.hero-arrow{position:absolute;top:164px;width:36px;height:36px;background:rgba(0,0,0,.55);display:flex;align-items:center;justify-content:center}
.hero-arrow.prev{left:20px}.hero-arrow.next{right:20px}
.hero-caption{position:absolute;left:68px;top:198px;color:var(--white)}
.hero-kicker{font-family:'Montserrat',sans-serif;font-size:8px;margin-bottom:3px}
.hero-title{font-family:'Roboto Slab',serif;font-weight:700;font-size:20px;line-height:25px;width:360px}
.btn{display:inline-block;font-family:'Montserrat',sans-serif;font-weight:700;font-size:9.5px;color:var(--white);border-radius:2px;text-align:center;line-height:22px;height:22px}
.btn-green{background:var(--green)}
.btn-red{background:var(--red)}
.hero .btn{margin-top:18px;width:65px}
.welcome{position:absolute;left:80px;top:464px;width:800px;text-align:center}
.welcome h1{font-family:'Roboto Slab',serif;font-weight:700;font-size:20px;color:var(--ink);margin-bottom:16px}
.welcome p{font-size:10px;line-height:16px;color:var(--text)}
.welcome .actions{margin-top:16px;display:flex;justify-content:center;gap:7px}
.welcome .btn{width:65px}
.special{position:absolute;left:75px;top:639px;width:616px;height:220px;background:var(--card);border-radius:4px}
.special h2{position:absolute;left:26px;top:19px;font-family:'Roboto Slab',serif;font-weight:700;font-size:20px;color:var(--ink)}
.special h3{position:absolute;left:26px;top:43px;font-family:'Montserrat',sans-serif;font-weight:400;font-size:14px;color:#4a4a4a}
.rating{position:absolute;left:26px;top:70px;display:flex;align-items:center;gap:1px;font-size:9px;color:#ccc}
.rating span{margin-left:6px}
.special p{position:absolute;left:26px;top:94px;width:350px;font-size:10px;line-height:13.5px;color:var(--text)}
.special .btn{position:absolute;left:26px;top:170px;width:65px}
.dish{position:absolute;left:392px;top:46px;width:196px;height:150px;border-radius:50%;background:radial-gradient(circle at 50% 45%,#e8622a 0%,#d14a1a 45%,#b88a3c 62%,transparent 66%)}
.ingredients{position:absolute;left:714px;top:639px;width:167px;height:220px;border-radius:4px;overflow:hidden;
  background:radial-gradient(circle at 20% 80%,#e0701a,transparent 45%),radial-gradient(circle at 80% 30%,#c22a1a,transparent 45%),linear-gradient(160deg,#5a2410,#8a3a14 50%,#2a1408);color:var(--white)}
.ingredients h4{font-family:'Roboto Slab',serif;font-weight:700;font-size:16px;text-align:center;margin-top:21px}
.ing-list{list-style:none;margin:16px 0 0 24px;font-family:'Montserrat',sans-serif;font-size:10px}
.ing-list li{display:flex;height:20.6px}
.ing-list b{width:40px;font-weight:400}
.ing-list .done{text-decoration:line-through;opacity:.6}
.dots{position:absolute;bottom:20px;left:0;right:0;display:flex;justify-content:center;gap:5px}
.dots i{width:5px;height:5px;border-radius:50%;background:rgba(255,255,255,.5)}
.dots i:first-child{background:var(--white)}
.contacts{position:absolute;left:80px;top:907px;width:800px;display:flex}
.contact{width:205px;text-align:center;border-left:1px dotted #ccc;height:176px}
.contact:first-child{border-left:none}
.contact-icon{width:83px;height:83px;margin:0 auto;border-radius:50%;background:var(--green);border:4px solid var(--green-dark);display:flex;align-items:center;justify-content:center;margin-top:-8px}
.contact h5{font-family:'Lato',sans-serif;font-weight:400;font-size:12.5px;color:var(--ink);margin-top:22px;margin-bottom:9px}
.contact p{font-size:9.5px;line-height:16.5px;color:var(--muted)}
.footer{position:absolute;left:0;top:1138px;width:960px;height:62px;background:var(--black)}
.social{position:absolute;left:80px;top:22px;display:flex;gap:17px}
.social i{width:17px;height:17px;border-radius:50%;background:#9a9a9a}
.copy{position:absolute;right:77px;top:24px;font-size:11.5px;color:#cfcfcf}
</style>
</head>
<body>
<div class="site">
  <div class="sheet"></div>

  <div class="brand"><span class="brand-dot"></span><span class="brand-name">Saffron Lane</span></div>
  <nav class="nav">
    <span class="active">Home</span><span>About Us</span><span>Services</span><span>Menu</span><span>Gallery</span><span>Contact</span>
  </nav>

  <section class="hero" role="img" aria-label="Buffet of Pakistani and Indian curries in steel pans">
    <div class="hero-arrow prev"><svg width="8" height="10" viewBox="0 0 8 10"><path d="M5.5 1.5 2 5l3.5 3.5" fill="none" stroke="#fff" stroke-width="1.4"/></svg></div>
    <div class="hero-arrow next"><svg width="8" height="10" viewBox="0 0 8 10"><path d="M2.5 1.5 6 5 2.5 8.5" fill="none" stroke="#fff" stroke-width="1.4"/></svg></div>
    <div class="hero-caption">
      <div class="hero-kicker">Saffron Lane</div>
      <div class="hero-title">We offer full service Pakistani and Indian food in Philadelphia, USA</div>
      <span class="btn btn-green">Recipe</span>
    </div>
  </section>

  <section class="welcome">
    <h1>Welcome To Saffron Lane</h1>
    <p>Curabitur suscipit, felis euismod laoreet venenatis, tellus nulla suscipit velit, efficitur venenatis risus erat at purus. Cras eleifend aliquet congue. Sed bibendum tellus at vehicula tincidunt. In fringilla, eros in luctus vulputate, libero dui tincidunt dui, vitae volutpat urna risus vel nibh. Sed dui sapien, rhoncus at est a, feugiat congue nibh. Nullam nisi leo, vehicula quis tincidunt a, sagittis ac sem. Quisque quis sagittis nisl, et luctus eros. Suspendisse vehicula risus vel blandit ornare. In hac habitasse platea dictumst. Proin diam tellus, vehicula et dui auctor, gravida posuere tortor. Donec malesuada lectus id ante porttitor tempor.</p>
    <div class="actions"><span class="btn btn-red">More</span><span class="btn btn-green">Book Now</span></div>
  </section>

  <section class="special">
    <h2>Today Special</h2>
    <h3>Tomatoes and Herbs</h3>
    <div class="rating">
      <svg width="82" height="14" viewBox="0 0 82 14" fill="none" stroke-width="0.9">
        <g stroke="#e0b040"><path d="M7 1l1.8 4 4.2.3-3.2 2.8 1 4.2L7 10l-3.8 2.3 1-4.2L1 5.3l4.2-.3z"/><path transform="translate(16 0)" d="M7 1l1.8 4 4.2.3-3.2 2.8 1 4.2L7 10l-3.8 2.3 1-4.2L1 5.3l4.2-.3z"/><path transform="translate(32 0)" d="M7 1l1.8 4 4.2.3-3.2 2.8 1 4.2L7 10l-3.8 2.3 1-4.2L1 5.3l4.2-.3z"/><path transform="translate(48 0)" d="M7 1l1.8 4 4.2.3-3.2 2.8 1 4.2L7 10l-3.8 2.3 1-4.2L1 5.3l4.2-.3z"/></g>
        <path stroke="#ccc" transform="translate(66 0)" d="M7 1l1.8 4 4.2.3-3.2 2.8 1 4.2L7 10l-3.8 2.3 1-4.2L1 5.3l4.2-.3z"/>
      </svg><span>4.1</span>
    </div>
    <p>Lorem ipsum dolor sit amet, consectetur adipiscing elit. Donec malesuada viverra nulla, nec fringilla quam laoreet maximus. Morbi dictum malesuada metus, sit amet consequat sem consequat vel. Pellentesque sollicitudin inter-dum libero sit amet iaculis.</p>
    <span class="btn btn-red">Recipe</span>
    <div class="dish" role="img" aria-label="Copper bowl of tomato and herb curry"></div>
  </section>

  <aside class="ingredients" role="img" aria-label="Ingredients list over a background of fresh vegetables">
    <h4>Ingredients</h4>
    <ul class="ing-list">
      <li class="done"><b>200g</b>fresh linguine</li>
      <li><b>2-3</b>cups tomatoes</li>
      <li><b>1/4</b>cup fresh herbs</li>
      <li><b>1-2</b>garlic cloves</li>
      <li><b>4</b>tablespoons oil</li>
      <li><b>1</b>spoon vinegar</li>
    </ul>
    <div class="dots"><i></i><i></i><i></i></div>
  </aside>

  <section class="contacts">
    <div class="contact">
      <div class="contact-icon"><svg width="22" height="22" viewBox="0 0 22 22" fill="none" stroke="#fff" stroke-width="1.3"><path d="M3 10 11 3l8 7"/><path d="M5 9v10h12V9"/><path d="M9 19v-5h4v5"/></svg></div>
      <h5>Address</h5>
      <p>482 Walnut Row, Suite 12,<br>Fairmount District, Philadelphia, PA, USA</p>
    </div>
    <div class="contact">
      <div class="contact-icon"><svg width="22" height="22" viewBox="0 0 22 22" fill="none" stroke="#fff" stroke-width="1.3"><rect x="2" y="5" width="18" height="12"/><path d="m2 5 9 7 9-7M2 17l7-6M20 17l-7-6"/></svg></div>
      <h5>Email</h5>
      <p>hello@saffronlane.com<br>orders@saffronlane.com</p>
    </div>
    <div class="contact">
      <div class="contact-icon"><svg width="22" height="22" viewBox="0 0 22 22" fill="none" stroke="#fff" stroke-width="1.3"><path d="M6 2 9 6 7 8.5c1 2.5 3.5 5 6.5 6.5L16 13l4 3-2 3.5C10 19 3 12 2.5 4z"/></svg></div>
      <h5>Phone Number</h5>
      <p>+1 215 555 0142<br>+1 215 555 0178<br>+1 215 555 0199</p>
    </div>
    <div class="contact">
      <div class="contact-icon"><svg width="22" height="22" viewBox="0 0 22 22" fill="none" stroke="#fff" stroke-width="1.3"><circle cx="11" cy="11" r="9"/><path d="M11 6v5h4"/></svg></div>
      <h5>Business Hours</h5>
      <p>Monday-Friday: 8am to 6pm<br>Saturday: 10am to 2pm<br>Sunday: Closed</p>
    </div>
  </section>

  <footer class="footer">
    <div class="social" aria-label="Social links"><i></i><i></i><i></i><i></i></div>
    <div class="copy">© vemrilo.com - All Rights Reserved</div>
  </footer>
</div>
</body>
</html>
```